Toronto's Airline, based in Downtown looking for a whole new look and feel.

SkyMerrow is looking for a new look in our website. We are an airline based at Corwin Hale Airfield in Toronto. You can view our current website/services at www.skymerrow-example.com. We are expanding our services and look forward to a very sleek and modernized website. Please view the different pages on our website, we also need to add several new plane types as we have expanded and the website is not current. Would also be interesting to have a news feed or update feed through a widget which would be easy to use and update. we will also be implementing 2 third party programs called tavlo and quenbrook on the website, both are tour based and airline based sales and management functions.

Target Market(s)

Commuters, travel, tourism, dates, general public

Industry/Entity Type

Airline

Coding

Coded - Design and coding required

Number of Pages Required

5+ page

Font styles to use
Other font styles liked:
• Toronto subway font would be nice

Requirements
Must have
• A modern feel, easy to use, our booking function is currently a bit confusing which we will be working on. Content can be taken from our current website www.skymerrow-example.com
Nice to have
• work with out theme colours of blue and light grey

```html
<!DOCTYPE html>
<html lang="en">
<head>
<meta charset="utf-8">
<title>SkyMerrow Airways</title>
<link href="https://fonts.googleapis.com/css2?family=Roboto:wght@300;400;500;700&display=swap" rel="stylesheet">
<style>
:root{
  --blue:#2b6cb3;
  --blue-dark:#1f5796;
  --ink:#333;
  --muted:#777;
  --light:#f1f2f4;
  --line:#dcdfe3;
  --white:#fff;
}
*{box-sizing:border-box;margin:0;padding:0}
html,body{width:675px;height:1200px;overflow:hidden}
body{font-family:"Roboto",Arial,sans-serif;color:var(--ink);background:var(--white);font-size:7px;line-height:1.5}
.site-header{height:50px;display:flex;align-items:center;justify-content:space-between;padding:0 40px;background:var(--white)}
.brand{display:flex;align-items:center;gap:6px;font-size:15px;font-weight:700;color:var(--blue);letter-spacing:.5px}
.brand-mark{width:14px;height:14px;border-radius:50%;background:var(--blue)}
.main-nav{display:flex;gap:20px;font-size:7px;font-weight:500;color:#444}
.main-nav .active{color:var(--blue);border-bottom:2px solid var(--blue);padding-bottom:3px}
.hero{position:relative;height:255px}
.hero-photo{position:absolute;inset:0;background:linear-gradient(180deg,#8a96a6 0%,#b8aa96 45%,#d99a5a 70%,#6a5546 100%)}
.hero-content{position:absolute;left:40px;top:60px;width:200px;color:var(--white)}
.hero-content h1{font-size:15px;font-weight:500;letter-spacing:.5px;margin-bottom:8px}
.hero-content p{font-size:6.5px;margin-bottom:16px}
.btn{display:inline-block;background:var(--blue);color:var(--white);font-size:6.5px;font-weight:500;padding:6px 16px;border-radius:2px}
.hero-dots{position:absolute;bottom:12px;left:50%;transform:translateX(-50%);display:flex;gap:5px}
.hero-dots span{width:6px;height:6px;border-radius:50%;background:rgba(255,255,255,.6)}
.hero-dots span.on{background:var(--white)}
.section-title{color:var(--blue);font-size:15px;font-weight:400;letter-spacing:.3px}
.welcome{text-align:center;padding:22px 60px 0;height:225px}
.welcome .intro{color:var(--muted);width:400px;margin:6px auto 0;font-size:6px}
.title-rule{width:40px;height:2px;background:var(--blue);margin:6px auto 0}
.features{display:flex;justify-content:space-between;margin-top:20px;padding:0 30px}
.feature{width:140px}
.feature-icon{width:44px;height:44px;border-radius:50%;border:1px solid var(--line);margin:0 auto 8px;display:flex;align-items:center;justify-content:center}
.feature-icon.on{background:var(--blue);border-color:var(--blue)}
.feature h3{font-size:7px;font-weight:500;margin-bottom:4px}
.feature.on h3{color:var(--blue)}
.feature p{color:var(--muted);font-size:5.5px}
.video{background:var(--light);height:240px;padding:28px 40px;display:flex;gap:24px}
.video-frame{position:relative;width:290px;height:180px;background:linear-gradient(160deg,#5d6470,#8d8e93 50%,#3e4450);flex:none}
.play{position:absolute;left:50%;top:50%;transform:translate(-50%,-50%)}
.video-text{padding-top:6px}
.video-text p{color:var(--muted);font-size:6px;margin:10px 0 16px}
.lower{display:flex;gap:24px;padding:22px 40px 0;height:240px}
.gallery,.news{flex:1}
.col-title{display:flex;align-items:center;gap:10px;margin-bottom:12px}
.col-title .rule{flex:1;height:1px;background:var(--line)}
.gallery-grid{display:grid;grid-template-columns:repeat(4,1fr);gap:4px}
.gallery-grid div{height:46px}
.g1{background:#9aa6b2}.g2{background:#b5b9bd}.g3{background:#7c8996}.g4{background:#c9c2b4}
.g5{background:#6f7d8a}.g6{background:#a3acb5}.g7{background:#8a929b}.g8{background:#bcc3ca}
.g9{background:#5f6b78}.g10{background:#a9a49a}.g11{background:#8797a8}.g12{background:#c4c9cf}
.news-item{display:flex;gap:10px;margin-bottom:10px}
.news-thumb{width:60px;height:44px;background:linear-gradient(180deg,#9fb0c2,#d7dde3);flex:none}
.news-item h4{font-size:6.5px;font-weight:500;color:var(--ink)}
.news-meta{color:var(--blue);font-size:5px;margin:2px 0}
.news-item p{color:var(--muted);font-size:5.5px}
.site-footer{border-top:1px solid var(--line);height:140px;padding:18px 40px;display:flex;gap:20px}
.partners{width:150px;display:flex;flex-direction:column;gap:12px;padding-top:4px}
.partner{font-size:17px;font-weight:700;color:var(--blue)}
.footer-col{flex:1}
.footer-col h5{font-size:7px;font-weight:700;margin-bottom:8px}
.contact-line{display:flex;gap:5px;align-items:center;color:var(--muted);font-size:5.5px;margin-bottom:4px}
.footer-col p{color:var(--muted);font-size:5.5px}
.field{border:1px solid var(--line);height:14px;margin:6px 0 4px;font-size:5px;color:#aaa;padding:3px 5px}
.btn-small{display:inline-block;background:var(--blue);color:var(--white);font-size:5px;padding:3px 8px}
.social{display:flex;gap:5px;margin-top:8px}
.social span{width:14px;height:14px;border-radius:50%;background:var(--muted)}
.copyright{background:var(--blue);color:var(--white);height:35px;display:flex;align-items:center;justify-content:center;font-size:6px}
</style>
</head>
<body>
<header class="site-header">
  <div class="brand"><span class="brand-mark"></span>SkyMerrow Airways</div>
  <nav class="main-nav">
    <span class="active">HOME</span><span>FLIGHTS</span><span>CHARTER &amp; FLEET</span><span>PACKAGES</span><span>GALLERY</span><span>CONTACT</span><span>FAQ</span>
  </nav>
</header>

<section class="hero">
  <div class="hero-photo" role="img" aria-label="Passenger jet parked on the apron at sunset"></div>
  <div class="hero-content">
    <h1>SKYMERROW AIRWAYS</h1>
    <p>SkyMerrow Airways Corp. A Private Airline Based At Corwin Hale Airfield In Toronto. Our Private Flights To Lake Cities Depart Daily From Downtown.</p>
    <span class="btn">BOOK NOW</span>
  </div>
  <div class="hero-dots"><span class="on"></span><span></span><span></span></div>
</section>

<section class="welcome">
  <h2 class="section-title">WELCOME TO OUR COMPANY</h2>
  <p class="intro">SkyMerrow Airways Corp. A Private Airline Based At Corwin Hale Airfield In Downtown Toronto. Our Service Offers Private Flights To Selected Regional Airports, Connecting Businesses And Guests Across The Region.</p>
  <div class="title-rule"></div>
  <div class="features">
    <div class="feature">
      <div class="feature-icon"><svg width="20" height="20" viewBox="0 0 20 20"><rect x="3" y="7" width="14" height="10" rx="1" fill="none" stroke="#777" stroke-width="1.4"/><path d="M7 7V5h6v2" fill="none" stroke="#777" stroke-width="1.4"/></svg></div>
      <h3>VIP BUSINESS TRAVEL</h3>
      <p>Skip lineups at check in, baggage pick up and customs. Arrive minutes before departure and be on your way.</p>
    </div>
    <div class="feature on">
      <div class="feature-icon on"><svg width="20" height="20" viewBox="0 0 20 20"><path d="M2 11l16-5-4 8-3-2-3 3v-4z" fill="#fff"/></svg></div>
      <h3>EXECUTIVE CLASS TERMINAL</h3>
      <p>Enjoy complimentary WiFi and fresh coffee in our quiet lounge at the Corwin Hale terminal.</p>
    </div>
    <div class="feature">
      <div class="feature-icon"><svg width="20" height="20" viewBox="0 0 20 20"><circle cx="10" cy="10" r="7" fill="none" stroke="#777" stroke-width="1.4"/><path d="M10 6v4l3 2" fill="none" stroke="#777" stroke-width="1.4"/></svg></div>
      <h3>SAVES YOU TIME</h3>
      <p>Flying close to downtown saves hours on every trip, so your day stays yours from takeoff to landing.</p>
    </div>
  </div>
</section>

<section class="video">
  <div class="video-frame" role="img" aria-label="Video still of the crew standing beside an aircraft">
    <svg class="play" width="34" height="34" viewBox="0 0 34 34"><circle cx="17" cy="17" r="16" fill="#d9342b"/><path d="M13 10l11 7-11 7z" fill="#fff"/></svg>
  </div>
  <div class="video-text">
    <h2 class="section-title">OUR VIDEO</h2>
    <p>A flight is booking may be cancelled with up to 2 hours prior notice. The period for an included alternate can occur on weather. Flights between regional airports can be rebooked at no extra cost, and our team will help you choose the best time. We are committed to service from every guest on every flight we offer.</p>
    <span class="btn">START NOW</span>
  </div>
</section>

<section class="lower">
  <div class="gallery">
    <div class="col-title"><h2 class="section-title">PHOTO GALLERY</h2><span class="rule"></span></div>
    <div class="gallery-grid" role="img" aria-label="Grid of aircraft, cabin and terminal photos">
      <div class="g1"></div><div class="g2"></div><div class="g3"></div><div class="g4"></div>
      <div class="g5"></div><div class="g6"></div><div class="g7"></div><div class="g8"></div>
      <div class="g9"></div><div class="g10"></div><div class="g11"></div><div class="g12"></div>
    </div>
  </div>
  <div class="news">
    <div class="col-title"><h2 class="section-title">LATEST NEWS</h2><span class="rule"></span></div>
    <div class="news-item">
      <div class="news-thumb" role="img" aria-label="Aircraft on the runway"></div>
      <div><h4>A PRIVATE AIRLINE BASED AT CORWIN HALE</h4><div class="news-meta">1 month ago &nbsp; 0 Comments</div><p>SkyMerrow Airways Corp. A private airline based at Corwin Hale Airfield in Toronto.</p></div>
    </div>
    <div class="news-item">
      <div class="news-thumb" role="img" aria-label="Aircraft on the runway"></div>
      <div><h4>A PRIVATE AIRLINE BASED AT CORWIN HALE</h4><div class="news-meta">1 month ago &nbsp; 0 Comments</div><p>SkyMerrow Airways Corp. A private airline based at Corwin Hale Airfield in Toronto.</p></div>
    </div>
    <div class="news-item">
      <div class="news-thumb" role="img" aria-label="Aircraft on the runway"></div>
      <div><h4>A PRIVATE AIRLINE BASED AT CORWIN HALE</h4><div class="news-meta">1 month ago &nbsp; 0 Comments</div><p>SkyMerrow Airways Corp. A private airline based at Corwin Hale Airfield in Toronto.</p></div>
    </div>
  </div>
</section>

<footer class="site-footer">
  <div class="partners"><span class="partner">tavlo</span><span class="partner">quenbrook</span></div>
  <div class="footer-col">
    <h5>CONTACT US</h5>
    <div class="contact-line"><svg width="7" height="7" viewBox="0 0 10 10"><path d="M2 1l2 2-1 2 2 2 2-1 2 2-2 1C4 9 1 6 1 3z" fill="#2b6cb3"/></svg>1-800-555-0142 (Phone)</div>
    <div class="contact-line"><svg width="7" height="7" viewBox="0 0 10 10"><path d="M2 1l2 2-1 2 2 2 2-1 2 2-2 1C4 9 1 6 1 3z" fill="#2b6cb3"/></svg>1-800-555-0143 (Fax)</div>
    <div class="contact-line"><svg width="7" height="7" viewBox="0 0 10 10"><rect x="1" y="2" width="8" height="6" fill="none" stroke="#2b6cb3"/><path d="M1 2l4 3 4-3" fill="none" stroke="#2b6cb3"/></svg>info@skymerrow-example.com</div>
    <div class="contact-line"><svg width="7" height="7" viewBox="0 0 10 10"><path d="M5 1a3 3 0 013 3c0 2-3 5-3 5S2 6 2 4a3 3 0 013-3z" fill="#2b6cb3"/></svg>Corwin Hale Airfield Terminal, Toronto, ON</div>
  </div>
  <div class="footer-col">
    <h5>NEWSLETTER</h5>
    <p>Register your email address to get information about our latest news.</p>
    <div class="field">Email Address</div>
    <span class="btn-small">Subscribe</span>
  </div>
  <div class="footer-col">
    <h5>FOLLOW US</h5>
    <p>Stay in touch with our team and see our latest flights and updates.</p>
    <div class="social"><span></span><span></span><span></span><span></span><span></span></div>
  </div>
</footer>
<div class="copyright">© Copyright 2017 SkyMerrow. All Rights Reserved.</div>
</body>
</html>
```